Gobal construction supply company needs new business card design

I need a business card design for my global supply company using an existing logo. i will be looking to print these on rounded corner cards with the black background version of my logo on the back. on the front white background, my logo again and my simple details.

```html
<!DOCTYPE html>
<html lang="en">
<head>
<meta charset="utf-8">
<title>Southern Crest Supply – Business Card</title>
<link rel="stylesheet" href="https://fonts.googleapis.com/css2?family=Montserrat:wght@500;600;700&family=Open+Sans:wght@400;600&display=swap">
<style>
  :root {
    --stage: #333333;
    --card-light: #f0f0f0;
    --brand-red: #d60000;
    --rule-red: #b80000;
    --ink: #111111;
    --ink-soft: #333333;
    --rule-grey: #9a9a9a;
    --white: #ffffff;
  }
  * { margin: 0; padding: 0; box-sizing: border-box; }
  html, body { width: 1200px; height: 900px; overflow: hidden; }
  body { background: var(--stage); position: relative; font-family: "Open Sans", Arial, sans-serif; }

  .card { position: absolute; width: 477px; height: 294px; }
  .card-front {
    left: 120px; top: 275px; background: var(--card-light);
    border-radius: 0 48px 0 48px;
  }
  .card-back {
    left: 606px; top: 273px; background: var(--brand-red);
    border-radius: 48px 0 48px 0;
  }

  .brand {
    position: absolute; display: flex; align-items: center; gap: 10px;
    font-family: "Montserrat", Arial, sans-serif; font-weight: 700;
    line-height: 1; letter-spacing: 0.3px; white-space: nowrap;
  }
  .brand-mark { flex: none; }

  .card-front .brand { right: 35px; top: 118px; color: var(--ink); font-size: 19px; }
  .card-front .brand-mark { width: 18px; height: 18px; background: var(--brand-red); }

  .card-back .brand { left: 0; right: 0; justify-content: center; top: 162px; color: var(--white); font-size: 21px; }
  .card-back .brand-mark { width: 20px; height: 20px; border-radius: 50%; background: var(--white); }

  .person { position: absolute; left: 29px; top: 178px; width: 418px; }
  .person-name {
    font-family: "Montserrat", Arial, sans-serif; font-weight: 600;
    font-size: 17px; color: var(--brand-red); line-height: 20px;
  }
  .person-role { display: flex; align-items: center; gap: 6px; font-size: 14px; color: var(--ink-soft); line-height: 16px; }
  .person-role::after { content: ""; flex: 1; height: 1px; background: var(--rule-grey); margin-top: 3px; }

  .contacts { position: absolute; top: 238px; font-size: 14px; color: var(--ink-soft); line-height: 17px; }
  .contacts-phone { left: 29px; }
  .contacts-web { right: 27px; text-align: right; }
  .contact-item { display: flex; align-items: center; gap: 5px; }
  .contacts-web .contact-item { justify-content: flex-end; }
  .icon { width: 11px; height: 11px; fill: var(--brand-red); flex: none; }

  .back-rule { position: absolute; left: 67px; top: 232px; width: 343px; height: 1px; background: var(--rule-red); }
  .back-url {
    position: absolute; left: 0; right: 0; top: 247px; text-align: center;
    color: var(--white); font-size: 13px; font-weight: 600;
  }
</style>
</head>
<body>
  <section class="card card-front" aria-label="Card front">
    <div class="brand">
      <span class="brand-mark"></span>
      <span class="brand-name">SOUTHERN CREST SUPPLY</span>
    </div>

    <div class="person">
      <p class="person-name">MARCUS HALE</p>
      <p class="person-role">Managing Director</p>
    </div>

    <div class="contacts contacts-phone">
      <p class="contact-item">
        <svg class="icon" viewBox="0 0 12 12" aria-hidden="true"><path d="M1 4.5C1 3 3 2 6 2s5 1 5 2.5v1H8.5V4.3H3.5v1.2H1z"/><path d="M2.5 6.5 4 5h4l1.5 1.5V10h-7z"/></svg>
        044-987 654 321
      </p>
      <p class="contact-item">
        <svg class="icon" viewBox="0 0 12 12" aria-hidden="true"><path d="M3 0.5h6a1 1 0 0 1 1 1v9a1 1 0 0 1-1 1H3a1 1 0 0 1-1-1v-9a1 1 0 0 1 1-1zm0.5 1.5v7h5V2z"/></svg>
        044-987 654 321
      </p>
    </div>

    <div class="contacts contacts-web">
      <p class="contact-item">
        hello@crestsupply.com
        <svg class="icon" viewBox="0 0 12 12" aria-hidden="true"><path d="M1 2.5h10v7H1z M1.6 3 6 6.5 10.4 3" stroke="#f0f0f0" stroke-width="0.9"/></svg>
      </p>
      <p class="contact-item">
        www.crestsupply.com
        <svg class="icon" viewBox="0 0 12 12" aria-hidden="true"><circle cx="6" cy="6" r="5.5"/><path d="M0.8 6h10.4M6 0.6c-2 2.8-2 8 0 10.8M6 0.6c2 2.8 2 8 0 10.8" fill="none" stroke="#f0f0f0" stroke-width="0.8"/></svg>
      </p>
    </div>
  </section>

  <section class="card card-back" aria-label="Card back">
    <div class="brand">
      <span class="brand-mark"></span>
      <span class="brand-name">SOUTHERN CREST SUPPLY</span>
    </div>
    <div class="back-rule"></div>
    <p class="back-url">www.crestsupply.com</p>
  </section>
</body>
</html>
```